Website Design for a holiday home letting busines

We require a redesign of our present website www.pinebrookstays.com. We want the website to stand out and look professional and clean to make holiday hunters want to book a caravan or lodge holiday with us. Our logo is red however we DO NOT want the website to be red. We want a natural colour scheme.

The final design should communicate that we are a professional company to book with.

On the home page we require;
Overview of company
Photo
Search box for holiday (check in)
Late Deals
Reviews
News

We would like the following pages designed; home page, available dates page, caravans page, content page.

The website should be responsive for smart phones. One website I do like is http://www.verdoliso.be/nl/

Target Market(s)

Families

Industry/Entity Type

Travel

Number of Pages Required

5+ page

Font styles to use
Serif

Requirements
Must have
• The project must be responsive for mobile phones and tablets.
• Ability to search for holiday home holidays
• We want a natural colour scheme.
Nice to have
• A style we like is http://www.verdoliso.be/nl/
Should not have
• Do not use red as a colour for the website. Our logo is red so this is the only time we want this used.

```html
<!DOCTYPE html>
<html lang="en">
<head>
<meta charset="utf-8">
<title>Pinebrook Stays – Private Holiday Rentals</title>
<link href="https://fonts.googleapis.com/css2?family=Open+Sans:wght@400;600;700&display=swap" rel="stylesheet">
<style>
:root{
  --gold:#cbb46b;
  --gold-dark:#b49d55;
  --ink:#3d3d3d;
  --muted:#7a7a7a;
  --nav:#6e6e6e;
  --band:#ececec;
  --footer:#4b4b4b;
  --footer-deep:#3a3a3a;
  --white:#ffffff;
  --hero-a:#8a7a68;
  --hero-b:#d8cfc3;
}
*{box-sizing:border-box;margin:0;padding:0}
html,body{width:1200px;height:2952px;overflow:hidden}
body{font-family:"Open Sans",Arial,sans-serif;color:var(--ink);background:var(--white);position:relative}
.wrap{width:1000px;margin:0 auto;position:relative}

/* header */
.site-header{height:100px;display:flex;align-items:center}
.site-header .wrap{display:flex;justify-content:space-between;align-items:center}
.brand{display:flex;align-items:center;gap:12px;font-size:26px;font-weight:700;color:var(--ink)}
.brand-dot{width:34px;height:34px;border-radius:50%;background:var(--ink)}
.brand-tag{display:block;font-size:11px;font-weight:400;color:var(--muted)}
.top-search{display:flex}
.top-search span{width:200px;height:30px;border:1px solid #ddd;font-size:12px;color:#aaa;padding:6px 10px}
.top-search i{width:30px;height:30px;background:var(--gold)}
.main-nav{height:44px;background:var(--nav)}
.main-nav ul{list-style:none;display:flex;justify-content:space-between;height:44px;width:1000px;margin:0 auto}
.main-nav li{color:var(--white);font-size:12px;padding:0 12px;line-height:44px;white-space:nowrap}
.main-nav li.active{background:var(--gold)}

/* hero */
.hero{height:640px;position:relative;background:linear-gradient(160deg,var(--hero-a),var(--hero-b) 60%,#efe9e0)}
.hero-copy{position:absolute;top:240px;left:0;right:0;text-align:center;color:var(--white)}
.hero-copy h1{font-size:40px;font-weight:600;letter-spacing:1px}
.hero-copy h1 em{font-style:normal;color:var(--gold)}
.hero-copy p{font-size:20px;margin-top:8px;line-height:1.4}
.booking{position:absolute;bottom:0;left:0;right:0;height:96px;background:rgba(60,55,50,.55)}
.booking .wrap{display:flex;gap:20px;align-items:center;height:96px;justify-content:center}
.field{width:200px;height:48px;background:var(--gold);color:var(--white);font-size:14px;font-weight:600;display:flex;align-items:center;justify-content:center}
.field.search{background:transparent;border:1px solid rgba(255,255,255,.4);width:220px}

/* sections */
.section-title{text-align:center;font-size:26px;font-weight:700;color:var(--ink);letter-spacing:.5px}
.welcome{padding:44px 0 0;text-align:center}
.welcome .section-title{font-size:22px;font-weight:600}
.welcome p{width:820px;margin:16px auto 0;font-size:13px;line-height:1.7;color:var(--muted)}
.btn-outline{display:inline-block;margin-top:18px;border:1px solid var(--gold);color:var(--gold-dark);font-size:11px;padding:5px 16px}

.cards{display:flex;gap:20px;margin-top:40px}
.card{width:320px;height:370px;background:var(--gold);position:relative}
.card-photo{height:300px;background:linear-gradient(150deg,#6f5d4a,#bda88f 55%,#e6ddd0)}
.card-name{height:70px;line-height:70px;text-align:center;color:var(--white);font-size:13px;font-weight:700;text-transform:uppercase}
.card .icons{position:absolute;top:16px;right:16px;display:flex;gap:10px}
.card .icons svg{width:22px;height:22px}
.card-detail{position:absolute;inset:0 0 70px 0;background:rgba(40,40,40,.78);padding:110px 30px 0;color:var(--white);font-size:13px}
.card-detail dl{display:grid;grid-template-columns:1fr 1fr;row-gap:10px}
.dots{display:flex;justify-content:center;gap:8px;margin-top:26px}
.dots i{width:9px;height:9px;border-radius:50%;background:#ccc}
.dots i.on{background:var(--gold)}

.deal .price{position:absolute;right:14px;top:240px;color:var(--white);font-size:28px;font-weight:700}
.deal .card-name{line-height:1.5;padding-top:14px;text-transform:none;font-weight:400}
.deal .card-name b{display:block;font-weight:600}

/* news band */
.news-band{position:absolute;top:2100px;left:0;right:0;height:500px;background:var(--band)}
.panels{display:flex;gap:20px;padding-top:40px}
.panel{width:320px;height:420px;background:var(--gold);padding:20px}
.panel h3{color:var(--white);font-size:22px;font-weight:600;margin-bottom:18px}
.item{display:flex;gap:12px;margin-bottom:22px;color:var(--white);font-size:11px;line-height:1.4}
.thumb{width:64px;height:54px;flex:none;background:linear-gradient(135deg,#6d6152,#b9ab97)}
.avatar{width:46px;height:46px;flex:none;background:#9a8b74}
.item b{display:block;font-size:12px}
.blog-photo{height:200px;background:linear-gradient(150deg,#7d6e5c,#d9cfc1)}
.panel .item.blog{display:block;margin-top:16px}

/* footer */
.site-footer{position:absolute;top:2600px;left:0;right:0;height:300px;background:var(--footer);color:#ddd}
.site-footer .wrap{display:flex;justify-content:space-between;padding-top:34px}
.site-footer h4{color:var(--white);font-size:22px;font-weight:700;margin-bottom:16px}
.quick ul{list-style:none;font-size:12px;line-height:22px}
.signup{width:360px;text-align:center;font-size:11px;line-height:1.5}
.signup .brand{justify-content:center;color:#bdbdbd;font-size:22px;margin-bottom:20px}
.signup .brand-dot{background:#8a8a8a;width:28px;height:28px}
.signup form{display:flex;justify-content:center;margin-top:14px}
.signup form span{width:200px;height:30px;background:var(--white);color:#aaa;text-align:left;padding:7px 8px}
.signup form i{width:30px;height:30px;background:var(--gold)}
.contact ul{list-style:none;font-size:12px;line-height:22px}
.contact li{display:flex;gap:8px;align-items:flex-start}
.contact svg{width:12px;height:12px;margin-top:5px;flex:none}
.bottom-bar{position:absolute;top:2900px;left:0;right:0;height:52px;background:var(--footer-deep);color:#aaa;font-size:11px}
.bottom-bar .wrap{display:flex;justify-content:space-between;align-items:center;height:52px}
.socials,.cards-pay{display:flex;gap:10px}
.socials i{width:14px;height:14px;border-radius:50%;background:var(--gold)}
.cards-pay i{width:34px;height:22px;background:#ddd}
</style>
</head>
<body>

<header class="site-header">
  <div class="wrap">
    <div class="brand"><span class="brand-dot"></span><span>Pinebrook Stays<span class="brand-tag">at Fernhollow Holiday Park</span></span></div>
    <div class="top-search"><span>Search</span><i></i></div>
  </div>
</header>

<nav class="main-nav">
  <ul>
    <li class="active">Home</li><li>News</li><li>Reviews</li><li>Caravans &amp; Lodges</li><li>2015 Holiday</li><li>2016 Holiday</li><li>Payment Plans</li><li>Fernhollow Info</li><li>Local Attractions</li><li>Contact Us</li>
  </ul>
</nav>

<section class="hero" role="img" aria-label="Photo of a bright caravan lounge with sofa and curtained windows">
  <div class="hero-copy">
    <h1>PRIVATE HOLIDAY <em>RENTALS</em></h1>
    <p>Quality Lodge &amp; Caravan hire at Fernhollow<br>Holiday Park. Book online today!</p>
  </div>
  <div class="booking">
    <div class="wrap">
      <div class="field">28 - 08 - 2015</div>
      <div class="field">CHECK OUT</div>
      <div class="field search">SEARCH</div>
    </div>
  </div>
</section>

<section class="welcome">
  <h2 class="section-title">WELCOME TO PINEBROOK STAYS</h2>
  <p>Would you like to book a 2015 caravan or lodge holiday at Fernhollow Holiday Park and SAVE up to 25%? We have flexible start and end dates with no extra fees, and every caravan is checked before you arrive. Pay online in stages with no booking fee, choose from family-friendly lodges close to the pool, beach and play areas, and relax knowing our team is on hand all season.</p>
  <span class="btn-outline">READ MORE</span>
</section>

<section class="wrap" style="margin-top:56px">
  <h2 class="section-title">OUR CARAVANS AND LODGES</h2>
  <div class="cards">
    <article class="card">
      <div class="card-photo" role="img" aria-label="Caravan interior lounge"></div>
      <div class="card-detail">
        <dl><dt>Caravan type</dt><dd>Lodge</dd><dt>Grade</dt><dd>Luxury Lodge</dd><dt>Sleeps</dt><dd>6</dd><dt>Bedrooms</dt><dd>3</dd></dl>
      </div>
      <div class="icons">
        <svg viewBox="0 0 24 24"><circle cx="10" cy="10" r="6" fill="none" stroke="#fff" stroke-width="2"/><path d="M15 15l6 6" stroke="#fff" stroke-width="2"/></svg>
        <svg viewBox="0 0 24 24"><path d="M9 15l6-6M7 11l-2 2a3 3 0 0 0 4 4l2-2M17 13l2-2a3 3 0 0 0-4-4l-2 2" fill="none" stroke="#fff" stroke-width="2"/></svg>
      </div>
      <div class="card-name">The Hartfield</div>
    </article>
    <article class="card">
      <div class="card-photo" role="img" aria-label="Caravan interior lounge"></div>
      <div class="card-name">The Ashcombe</div>
    </article>
    <article class="card">
      <div class="card-photo" role="img" aria-label="Caravan interior lounge"></div>
      <div class="card-name">The Linwood</div>
    </article>
  </div>
  <div class="dots"><i class="on"></i><i></i></div>
</section>

<section class="wrap" style="margin-top:58px">
  <h2 class="section-title">LATE DEALS</h2>
  <div class="cards">
    <article class="card deal">
      <div class="card-photo" role="img" aria-label="Caravan interior"></div>
      <span class="price">£140.00</span>
      <div class="card-name"><b>The Marlow</b>Friday 04 September 2015 (3 nights)</div>
    </article>
    <article class="card deal">
      <div class="card-photo" role="img" aria-label="Caravan interior"></div>
      <span class="price">£275.00</span>
      <div class="card-name"><b>The Ashcombe</b>Friday 04 September 2015 (7 nights)</div>
    </article>
    <article class="card deal">
      <div class="card-photo" role="img" aria-label="Caravan interior"></div>
      <span class="price">£140.00</span>
      <div class="card-name"><b>The Brambleton</b>Friday 11 September 2015 (3 nights)</div>
    </article>
  </div>
  <div class="dots"><i class="on"></i><i></i></div>
</section>

<section class="news-band">
  <div class="wrap panels">
    <div class="panel">
      <h3>Recent News</h3>
      <div class="item"><div class="thumb" role="img" aria-label="News photo"></div><div><b>Park Pool Reopens</b>Fresh facilities ready for the new season.</div></div>
      <div class="item"><div class="thumb" role="img" aria-label="News photo"></div><div><b>Autumn Offers Live</b>Short breaks now open for booking.</div></div>
      <div class="item"><div class="thumb" role="img" aria-label="News photo"></div><div><b>New Lodges Arrive</b>Three luxury lodges join our fleet.</div></div>
      <div class="item"><div class="thumb" role="img" aria-label="News photo"></div><div><b>Family Fun Week</b>Games and shows every evening.</div></div>
    </div>
    <div class="panel">
      <h3>Community feed</h3>
      <div class="item"><div class="avatar" role="img" aria-label="Guest profile picture"></div><div><b>Guest Review</b>Lovely clean caravan, will book again.</div></div>
      <div class="item"><div class="avatar" role="img" aria-label="Guest profile picture"></div><div><b>Guest Review</b>Great location near the beach path.</div></div>
      <div class="item"><div class="avatar" role="img" aria-label="Guest profile picture"></div><div><b>Guest Review</b>Friendly team and easy check in.</div></div>
      <div class="item"><div class="avatar" role="img" aria-label="Guest profile picture"></div><div><b>Guest Review</b>The kids loved every single day.</div></div>
    </div>
    <div class="panel">
      <h3>Blog</h3>
      <div class="blog-photo" role="img" aria-label="Photo of a lodge bedroom"></div>
      <div class="item blog"><b>Fernhollow Lodge Week</b>A look inside our newest lodges and what families can expect on arrival.</div>
    </div>
  </div>
</section>

<footer class="site-footer">
  <div class="wrap">
    <div class="quick">
      <h4>QUICK LINK</h4>
      <ul><li>Home</li><li>News</li><li>Reviews</li><li>Caravans &amp; Lodges</li><li>2015 Holiday &amp; 2016 Holiday</li><li>Payment Plans</li><li>Fernhollow Info</li><li>Local Attractions</li><li>Contact Us</li></ul>
    </div>
    <div class="signup">
      <div class="brand"><span class="brand-dot"></span>Pinebrook Stays</div>
      <p>By subscribing to our company newsletter you will always be up to date on our latest promotions and deals.</p>
      <form><span>Email Address</span><i></i></form>
    </div>
    <div class="contact">
      <h4>CONTACT US</h4>
      <ul>
        <li><svg viewBox="0 0 12 12"><path d="M2 1l2 0 1 3-1.5 1a6 6 0 0 0 3.5 3.5L8 7l3 1v2a1 1 0 0 1-1 1A9 9 0 0 1 1 2a1 1 0 0 1 1-1z" fill="#cbb46b"/></svg>01632 960 418</li>
        <li><svg viewBox="0 0 12 12"><rect x="1" y="3" width="10" height="7" fill="none" stroke="#cbb46b"/><path d="M1 3l5 4 5-4" fill="none" stroke="#cbb46b"/></svg>hello@pinebrookstays.com</li>
        <li><svg viewBox="0 0 12 12"><path d="M6 11S2 7 2 4.5a4 4 0 0 1 8 0C10 7 6 11 6 11z" fill="#cbb46b"/></svg>Pinebrook Stays Ltd<br>4 Alder Court<br>Millbrook Trading Estate<br>Northshire NE1 7QT</li>
      </ul>
    </div>
  </div>
</footer>

<div class="bottom-bar">
  <div class="wrap">
    <span>© 2015 Pinebrook Stays. All rights reserved.</span>
    <div class="socials"><i></i><i></i><i></i></div>
    <div class="cards-pay"><i></i><i></i></div>
  </div>
</div>

</body>
</html>
```